Business card design for holistic health care clinic

We need a double-sided business card design for our holistic health care clinic that integrates our logo design and also its color scheme. My business is called Valmira. It is an integrative medicine clinic. You have already done the logo for me. Please ensure an elegant and upscale design that is not cluttered, but still has all the necessary information (please see below for details).

Target Market(s)

Wellness, fitness, rehabilitation for educated, well-traveled open-minded clients who are focused on natural, organic, balanced and preventive healthcare and lifestyle.

Industry/Entity Type

Medical

Contact Information for Business Card

Modern, clean.

Number of Pages Required

1 page

Font styles to use
Serif
Sans Serif

Colors

Designer to choose colors to be used in the design.

Requirements
Must have
• Logo on one side, all other information on the other side.
• Other information should include:
• Tobias Wrenfeld - DOE, CPT, LMT
• 4100 East Marrow Drive
• Austin, TX 78119
• 512 555 0148
• 818 555 0192
• info@ValmiraHealth.example
• t.wrenfeld@ValmiraHealth.example
Nice to have
• Darker background on front - but not totally black - shaded/dark gray.

```html
<!DOCTYPE html>
<html lang="en">
<head>
<meta charset="utf-8">
<title>Valmira Business Card</title>
<link href="https://fonts.googleapis.com/css2?family=Quicksand:wght@700&family=Work+Sans:wght@400;500&display=swap" rel="stylesheet">
<style>
  :root {
    --page: #141414;
    --card: #2a2a2b;
    --card-edge: #232324;
    --brand-blue: #1b8fd3;
    --text-light: #f2f2f2;
  }
  * { margin: 0; padding: 0; box-sizing: border-box; }
  html, body { width: 1200px; height: 900px; overflow: hidden; }
  body {
    background: var(--page);
    font-family: "Work Sans", Arial, sans-serif;
    color: var(--text-light);
    position: relative;
  }
  .card {
    position: absolute;
    left: 260px;
    width: 680px;
    height: 388px;
    background: linear-gradient(135deg, var(--card) 0%, #333334 55%, var(--card-edge) 100%);
    border-bottom: 9px solid var(--brand-blue);
    overflow: hidden;
  }
  .card--front { top: 50px; }
  .card--back { top: 462px; }

  .brand-name {
    font-family: "Quicksand", Arial, sans-serif;
    font-weight: 700;
    color: var(--brand-blue);
    line-height: 1;
    letter-spacing: 1px;
  }
  .brand-tagline {
    font-family: "Quicksand", Arial, sans-serif;
    font-weight: 700;
    color: var(--brand-blue);
  }

  /* Front */
  .front-logo {
    position: absolute;
    top: 110px;
    left: 0; right: 0;
    text-align: center;
  }
  .front-logo .brand-name { font-size: 96px; }
  .front-logo .brand-tagline { font-size: 25px; margin-top: 6px; letter-spacing: 0.5px; }
  .front-web {
    position: absolute;
    bottom: 26px;
    left: 0; right: 0;
    text-align: center;
    font-size: 15px;
    letter-spacing: 2px;
  }
  .accent { color: var(--brand-blue); }

  /* Back */
  .back-identity {
    position: absolute;
    top: 112px;
    left: 24px;
    width: 304px;
    text-align: center;
  }
  .back-identity .brand-name { font-size: 64px; }
  .back-identity .brand-tagline { font-size: 17px; margin-top: 4px; }
  .address {
    margin-top: 22px;
    font-size: 16px;
    line-height: 1.3;
    letter-spacing: 0.5px;
  }
  .divider {
    position: absolute;
    left: 348px;
    top: 92px;
    width: 2px;
    height: 200px;
    background: var(--brand-blue);
  }
  .person {
    position: absolute;
    left: 372px;
    top: 92px;
    width: 288px;
  }
  .person-name {
    font-family: "Work Sans", Arial, sans-serif;
    font-weight: 500;
    font-size: 24px;
    letter-spacing: 2px;
    color: var(--brand-blue);
    text-transform: uppercase;
    white-space: nowrap;
  }
  .person-title { font-size: 16px; letter-spacing: 1px; margin-top: 2px; }
  .contact-list { list-style: none; margin-top: 22px; }
  .contact-list li {
    display: flex;
    align-items: center;
    gap: 10px;
    font-size: 13.5px;
    letter-spacing: 0.3px;
    line-height: 24px;
    white-space: nowrap;
  }
  .contact-list svg { width: 14px; height: 14px; flex: none; fill: var(--brand-blue); }
</style>
</head>
<body>

<section class="card card--front" aria-label="Card front">
  <div class="front-logo">
    <div class="brand-name">VALMIRA</div>
    <div class="brand-tagline">Integrative Holistic Medicine</div>
  </div>
  <div class="front-web">www.<span class="accent">valmirahealth</span>.example</div>
</section>

<section class="card card--back" aria-label="Card back">
  <div class="back-identity">
    <div class="brand-name">VALMIRA</div>
    <div class="brand-tagline">Integrative Holistic Medicine</div>
    <p class="address">4100 East Marrow Drive<br>Austin, TX 78119</p>
  </div>

  <div class="divider"></div>

  <div class="person">
    <div class="person-name">Tobias Wrenfeld</div>
    <div class="person-title">DOE, CPT, LMT</div>
    <ul class="contact-list">
      <li>
        <svg viewBox="0 0 24 24" aria-hidden="true"><path d="M6.6 10.8a15 15 0 0 0 6.6 6.6l2.2-2.2c.3-.3.7-.4 1-.2 1.1.4 2.3.6 3.6.6.6 0 1 .4 1 1V20c0 .6-.4 1-1 1A17 17 0 0 1 3 4c0-.6.4-1 1-1h3.5c.6 0 1 .4 1 1 0 1.3.2 2.5.6 3.6.1.3 0 .7-.2 1z"/></svg>
        <span>512 555 0148</span>
      </li>
      <li>
        <svg viewBox="0 0 24 24" aria-hidden="true"><path d="M7 1h10a2 2 0 0 1 2 2v18a2 2 0 0 1-2 2H7a2 2 0 0 1-2-2V3a2 2 0 0 1 2-2zm0 3v14h10V4zm5 15.5a1 1 0 1 0 0 2 1 1 0 0 0 0-2z"/></svg>
        <span>818 555 0192</span>
      </li>
      <li>
        <svg viewBox="0 0 24 24" aria-hidden="true"><path d="M2 5h20v14H2zm2 2v.5l8 5 8-5V7zm0 2.8V17h16V9.8l-8 5z"/></svg>
        <span>info@ValmiraHealth.example</span>
      </li>
      <li>
        <svg viewBox="0 0 24 24" aria-hidden="true"><path d="M2 5h20v14H2zm2 2v.5l8 5 8-5V7zm0 2.8V17h16V9.8l-8 5z"/></svg>
        <span>t.wrenfeld@ValmiraHealth.example</span>
      </li>
      <li>
        <svg viewBox="0 0 24 24" aria-hidden="true"><path d="M12 2a10 10 0 1 0 0 20 10 10 0 0 0 0-20zm6.9 6h-2.9a15 15 0 0 0-1.4-3.9A8 8 0 0 1 18.9 8zM12 4c.8 1.2 1.5 2.5 1.9 4h-3.8c.4-1.5 1.1-2.8 1.9-4zM4.3 14a8 8 0 0 1 0-4h3.4a16 16 0 0 0 0 4zm.8 2h2.9c.3 1.4.8 2.7 1.4 3.9A8 8 0 0 1 5.1 16zM8 8H5.1a8 8 0 0 1 4.3-3.9C8.8 5.3 8.3 6.6 8 8zm4 12c-.8-1.2-1.5-2.5-1.9-4h3.8c-.4 1.5-1.1 2.8-1.9 4zm2.3-6H9.7a14 14 0 0 1 0-4h4.6a14 14 0 0 1 0 4zm.3 5.9c.6-1.2 1.1-2.5 1.4-3.9h2.9a8 8 0 0 1-4.3 3.9zm1.7-5.9a16 16 0 0 0 0-4h3.4a8 8 0 0 1 0 4z"/></svg>
        <span>www.<span class="accent">valmirahealth</span>.example</span>
      </li>
    </ul>
  </div>
</section>

</body>
</html>
```